Health Clinic treating people with mental illness needs a website

We need a website for a new mental health clinic based in Florida called Solvane Wellness USA. We treat people with mental health issues such as depression, PTSD, Bipolar, chronic pain, etc. I want the website to be easy to follow and inviting to the visitors. It should be easy to locate the different treatment options and how to go about contacting and making appointments. The images on the website should be something that the patients can relate to, whether a close up of a woman's face, something that conveys emotion. The patients visiting this website are often sad and miserable, they need to be able to feel comfortable when they look at this website. I want them to feel that we understand where they are coming from. I like colors such as purple, turquoise, lavender.

Target Market(s)

College students, veterans, anyone with mental illness

Industry/Entity Type

Health And Wellness

Font styles to use
Serif
Sans Serif

Colors

Designer to choose colors to be used in the design.

Requirements
Must have
• There should be a home/landing page, about us page, treatment page, contact page, and a FAQ page. I've included my logo below.
Nice to have
• The flow of the web pages should be calming and welcoming. I want people to feel warm and understood when they enter our page.
Should not have
• The images and writing should not be overly stimulating or aggressive.

```html
<!DOCTYPE html>
<html lang="en">
<head>
<meta charset="utf-8">
<title>Solvane Wellness USA</title>
<link href="https://fonts.googleapis.com/css2?family=Montserrat:ital,wght@0,400;0,500;0,600;1,400&family=Open+Sans:wght@400;600&display=swap" rel="stylesheet">
<style>
:root{
  --ink:#222;
  --muted:#555;
  --mint:#c4f0e6;
  --teal:#7ccbbd;
  --teal-deep:#2aa88a;
  --purple:#4a1f6e;
  --pink:#a33b96;
  --lilac:#eccbe6;
  --grey:#f0f0f0;
  --white:#fff;
}
*{margin:0;padding:0;box-sizing:border-box}
html,body{width:1200px;height:2529px;overflow:hidden;background:var(--white)}
body{position:relative;font-family:"Open Sans",sans-serif;color:var(--ink)}
.abs{position:absolute}
.head{font-family:"Montserrat",sans-serif}

/* header */
.brand{left:144px;top:40px;font-family:"Montserrat",sans-serif;font-weight:500;font-size:22px;color:var(--purple);display:flex;align-items:center;gap:8px}
.brand-dot{width:14px;height:14px;border-radius:50%;background:var(--teal)}
.book{left:880px;top:0;width:176px;height:43px;background:var(--teal);color:var(--ink);font-family:"Montserrat",sans-serif;font-size:13.5px;display:flex;align-items:center;justify-content:center}
.nav{top:68px;left:528px;display:flex;gap:34px;font-family:"Montserrat",sans-serif;font-size:13px;color:#444}
.nav .active{color:var(--pink)}
.nav .phone{color:#222;display:flex;align-items:center;gap:4px}

/* hero */
.hero-text{left:0;top:103px;width:600px;height:511px;background:var(--mint)}
.hero-photo{left:600px;top:103px;width:600px;height:511px;background:linear-gradient(135deg,#cfcac2 0%,#b89a6c 45%,#8d7a66 70%,#d9b642 100%)}
.hero-title{left:171px;top:206px;width:400px;text-align:center;font-family:"Montserrat",sans-serif;font-size:42px;line-height:56px;font-weight:400;color:var(--ink)}
.hero-sub{left:171px;top:380px;width:400px;text-align:center;font-size:13.5px}
.hero-arrow{left:361px;top:476px}

/* about */
.about-bg{left:0;top:614px;width:1200px;height:552px;background:var(--grey)}
.eyebrow{left:0;width:1200px;text-align:center;font-family:"Montserrat",sans-serif;font-style:italic;font-size:19px;color:#444}
.about-title{left:0;top:716px;width:1200px;text-align:center;font-family:"Montserrat",sans-serif;font-weight:600;font-size:33px;color:var(--teal-deep)}
.about-copy{left:144px;top:782px;width:912px;text-align:center;font-size:12.5px;line-height:22.5px;color:#333}
.about-arrow{left:588px;top:906px}
.about-photo{left:400px;top:967px;width:400px;height:400px;background:linear-gradient(160deg,#dfe2e8 0%,#c9c9cc 40%,#b59086 65%,#e9e9ee 100%)}

/* services */
.card{top:1447px;width:304px;height:298px;text-align:center}
.card .num{margin-top:50px;font-family:"Montserrat",sans-serif;font-style:italic;font-size:20px;color:#333}
.card h3{font-family:"Montserrat",sans-serif;font-weight:500;font-size:24px;margin-top:6px;color:#222}
.card p{font-size:12px;line-height:21px;margin:14px auto 0;width:254px;color:#333}
.c1{left:144px;background:var(--lilac)}
.c2{left:448px;background:var(--grey)}
.c3{left:752px;background:var(--mint)}
.more{display:inline-flex;align-items:center;gap:6px;margin-top:26px;margin-left:18px}
.more span{background:var(--teal);color:#222;font-size:12px;padding:9px 7px}

/* articles */
.articles-bg{left:0;top:1825px;width:1200px;height:602px;background:var(--grey)}
.panel{left:144px;top:1947px;width:912px;height:400px;background:var(--white)}
.post{top:1980px;width:280px;height:279px;border:1px solid #e3e3e3;background:var(--white)}
.post .img{height:160px}
.post h4{font-family:"Montserrat",sans-serif;font-weight:400;font-size:16px;padding:24px 0 0 22px;color:#333;height:70px}
.post .meta{margin:0 12px;border-top:1px solid #ddd;padding-top:14px;display:flex;align-items:center;font-size:11.5px;color:#333}
.post .meta .eye{display:flex;align-items:center;gap:6px;margin-left:2px;width:52px}
.post .meta .like{margin-left:auto;margin-right:2px}
.p1{left:160px}.p2{left:460px}.p3{left:760px}
.i1{background:linear-gradient(180deg,#e8ddd8 0%,#b57a50 55%,#3a2c2a 100%)}
.i2{background:linear-gradient(120deg,#e7c57a 0%,#e6e2d9 50%,#4d6ab3 100%)}
.i3{background:linear-gradient(135deg,#0e2a33 0%,#2f6b77 50%,#0b1f26 100%)}
.more-articles{left:160px;top:2281px;width:120px;height:35px;background:var(--teal);font-size:12px;display:flex;align-items:center;justify-content:center}

/* footer */
.social{left:144px;top:2471px;display:flex;gap:22px}
.social span{width:18px;height:18px;border-radius:50%;background:#555}
.copyright{right:145px;top:2473px;font-size:11.5px;color:#444}
</style>
</head>
<body>

<header>
  <div class="abs brand"><span class="brand-dot"></span>Solvane Wellness USA</div>
  <a class="abs book">Book an Appointment</a>
  <nav class="abs nav">
    <span class="active">Home</span><span>About Us</span><span>Treatment</span><span>FAQ</span><span>Contact Us</span>
    <span class="phone"><svg width="10" height="10" viewBox="0 0 24 24"><path fill="#222" d="M6.6 10.8a15 15 0 0 0 6.6 6.6l2.2-2.2c.3-.3.7-.4 1-.2 1.1.4 2.3.6 3.6.6.6 0 1 .4 1 1V20c0 .6-.4 1-1 1A17 17 0 0 1 3 4c0-.6.4-1 1-1h3.5c.6 0 1 .4 1 1 0 1.3.2 2.5.6 3.6.1.3 0 .7-.2 1z"/></svg>555 014 2270</span>
  </nav>
</header>

<section>
  <div class="abs hero-text"></div>
  <div class="abs hero-photo" role="img" aria-label="Close-up portrait of a smiling woman with wavy blonde hair seated in a yellow chair"></div>
  <h1 class="abs hero-title">Suspendisse Feugiat Purus Metus</h1>
  <p class="abs hero-sub">Interdum et malesuada fames</p>
  <svg class="abs hero-arrow" width="12" height="22" viewBox="0 0 12 22"><path d="M6 0v17" stroke="#222" stroke-width="3"/><path d="M0 14l6 8 6-8z" fill="#222"/></svg>
</section>

<section>
  <div class="abs about-bg"></div>
  <p class="abs eyebrow" style="top:690px">About</p>
  <h2 class="abs about-title">Solvane Wellness</h2>
  <p class="abs about-copy">Suspendisse potenti. Suspendisse feugiat purus metus, nec interdum elit dignissim eget. Pellentesque habitant morbi tristique senectus et netus et malesuada fames ac turpis egestas. Etiam fermentum ipsum ullamcorper ullamcorper aliquet. Nulla sed dolor auctor, porta ex in, laoreet odio. Aliquam sed felis dui. Ut luctus ut eros malesuada blandit. Praesent scelerisque fermentum mauris ut posuere. Curabitur non risus sed ante rhoncus semper. Praesent blandit, neque at porta sodales, ex diam tempus mi, eu fringilla odio leo at diam.</p>
  <svg class="abs about-arrow" width="24" height="12" viewBox="0 0 24 12"><path d="M0 6h18" stroke="#222" stroke-width="3"/><path d="M15 0l9 6-9 6z" fill="#222"/></svg>
  <div class="abs about-photo" role="img" aria-label="A doctor in a white coat talking kindly with a mother and daughter in a clinic room"></div>
</section>

<section>
  <div class="abs card c1"><p class="num">01</p><h3>Depression</h3><p>Suspendisse dapibus eros massa, ac iaculis ipsum venenatis sed. Pellentesque scelerisque auctor erat, at faucibus enim sollicitudin condimentum tortor metus.</p></div>
  <div class="abs card c2"><p class="num">02</p><h3>PTSD</h3><p>Suspendisse dapibus eros massa, ac iaculis ipsum venenatis sed. Pellentesque scelerisque auctor erat, at faucibus enim sollicitudin condimentum tortor metus.</p>
    <a class="more"><span>View More Services</span><svg width="16" height="10" viewBox="0 0 16 10"><path d="M0 5h11" stroke="#222" stroke-width="2.4"/><path d="M9 0l7 5-7 5z" fill="#222"/></svg></a></div>
  <div class="abs card c3"><p class="num">03</p><h3>Bipolar</h3><p>Suspendisse dapibus eros massa, ac iaculis ipsum venenatis sed. Pellentesque scelerisque auctor erat, at faucibus enim sollicitudin condimentum tortor metus.</p></div>
</section>

<section>
  <div class="abs articles-bg"></div>
  <p class="abs eyebrow" style="top:1900px">Articles about Psychology</p>
  <div class="abs panel"></div>
  <article class="abs post p1"><div class="img i1" role="img" aria-label="Silhouette of a woman's profile filled with a sunset over the sea"></div><h4>Understanding PTSD</h4><div class="meta"><span class="eye"><svg width="16" height="10" viewBox="0 0 16 10"><ellipse cx="8" cy="5" rx="8" ry="5" fill="#bbb"/><circle cx="8" cy="5" r="2.3" fill="#fff"/></svg>0</span>Write comment<svg class="like" width="16" height="14" viewBox="0 0 16 14"><path d="M8 14L1.5 7.5A4 4 0 0 1 8 2.5a4 4 0 0 1 6.5 5z" fill="#aaa"/></svg></div></article>
  <article class="abs post p2"><div class="img i2" role="img" aria-label="A doctor at a desk consulting with an older woman patient"></div><h4>Understanding PTSD</h4><div class="meta"><span class="eye"><svg width="16" height="10" viewBox="0 0 16 10"><ellipse cx="8" cy="5" rx="8" ry="5" fill="#bbb"/><circle cx="8" cy="5" r="2.3" fill="#fff"/></svg>0</span>Write comment<svg class="like" width="16" height="14" viewBox="0 0 16 14"><path d="M8 14L1.5 7.5A4 4 0 0 1 8 2.5a4 4 0 0 1 6.5 5z" fill="#aaa"/></svg></div></article>
  <article class="abs post p3"><div class="img i3" role="img" aria-label="Digital illustration of a person with a glowing brain on a dark teal background"></div><h4>Understanding PTSD</h4><div class="meta"><span class="eye"><svg width="16" height="10" viewBox="0 0 16 10"><ellipse cx="8" cy="5" rx="8" ry="5" fill="#bbb"/><circle cx="8" cy="5" r="2.3" fill="#fff"/></svg>0</span>Write comment<svg class="like" width="16" height="14" viewBox="0 0 16 14"><path d="M8 14L1.5 7.5A4 4 0 0 1 8 2.5a4 4 0 0 1 6.5 5z" fill="#aaa"/></svg></div></article>
  <a class="abs more-articles">More Articles</a>
</section>

<footer>
  <div class="abs social"><span aria-label="Social profile"></span><span aria-label="Social profile"></span></div>
  <p class="abs copyright">Copyright &copy; 2019 Solvane Wellness.&nbsp;&nbsp; All rights reserved.</p>
</footer>

</body>
</html>
```